Austin TX First Veterinary Urgent Care

We need a flyer designed for us and our clinic that is eye-catching but also summarizes the advantages of our services. We want to express that we are family owned, have convenient hours and affordable prices. We are the first veterinary urgent care animal clinic in Austin Texas. Our hours of operation are M-F 12PM-9PM S-S 10AM-6PM. Our Address is 4871 W Larkspur Rd Suite B212 Austin, Tx 78753. Our phone number is (737)555-0148 our website is www.brookpawclinic.com and our email address is info@brookpawclinic.com.

Target Market(s)

Pet owners and veterinary professionals for referral purposes.

Industry/Entity Type

Veterinary

Font styles to use
Sans Serif

Colors
0094D4
00A9DD
6FCCEA
C7EBF8
E9F6FB
00AB8E
00BBA5
67D7C9
C6EFE9
E9F9F6

Requirements
Must have
• Our logo, hours of operation and contact information easy to read. Should emphasize that we are affordable as well as family owned. List of services should also be displayed: ear, eye, and skin issues, limping, broken toenails, lacerations, coughing, sneezing, allergies, vomiting and diarrhea, urinary issues, constipation, snake bites, toxin ingestion, and many many more
Nice to have
• We would like to have a modern feel with drawn/cartoon images, not realistic stock photos of dogs/cats.

```html
<!DOCTYPE html>
<html lang="en">
<head>
<meta charset="utf-8">
<title>BrookPaw Vet – Veterinary Urgent Care Flyer</title>
<link rel="stylesheet" href="https://fonts.googleapis.com/css2?family=Poppins:wght@400;500;600;700;800&family=Montserrat:wght@400;500&display=swap">
<style>
  :root {
    --green: #3fa34d;
    --green-bright: #35b34a;
    --navy: #0d0f8f;
    --blue-accent: #1b2fd8;
    --ink: #0e0f12;
    --white: #ffffff;
    --page: #f2f3f5;
  }
  * { margin: 0; padding: 0; box-sizing: border-box; }
  html, body { width: 1200px; height: 2333px; overflow: hidden; }
  body { background: var(--page); font-family: "Poppins", sans-serif; position: relative; }

  .flyer {
    position: absolute; left: 100px; top: 518px;
    width: 1000px; height: 1296px;
    background: var(--green); overflow: hidden;
    box-shadow: 0 10px 30px rgba(0,0,0,.18);
  }
  .abs { position: absolute; white-space: nowrap; }

  .brand { left: 62px; top: 78px; display: flex; align-items: center; gap: 14px; }
  .brand-dot { width: 58px; height: 58px; border-radius: 50%; background: var(--white); }
  .brand-name { font-weight: 800; font-size: 48px; color: var(--navy); line-height: 1; }

  .headline-top { left: 60px; top: 206px; font-weight: 800; font-size: 54px; color: var(--white); line-height: 1; }
  .headline-main { left: 58px; top: 256px; font-weight: 800; font-size: 71px; color: var(--navy); line-height: 1; }
  .headline-sub { left: 62px; top: 330px; font-family: "Montserrat", sans-serif; font-weight: 500; font-size: 46px; color: var(--white); letter-spacing: 10px; line-height: 1; }
  .tagline { left: 62px; top: 386px; font-size: 19px; color: var(--white); line-height: 1.2; font-weight: 400; }

  .promise { left: 62px; top: 466px; display: flex; align-items: center; gap: 22px; }
  .promise-text { color: var(--white); font-weight: 500; line-height: 1; }
  .promise-text .l1 { font-size: 38px; display: block; }
  .promise-text .l1 b { color: var(--navy); font-weight: 700; }
  .promise-text .l2 { font-size: 28px; display: block; margin-top: 2px; }

  .services-title { left: 62px; top: 586px; font-weight: 600; font-size: 35px; color: var(--white); line-height: 1; }
  .services-title b { color: var(--navy); font-weight: 700; }
  .services-rule { left: 62px; top: 636px; width: 504px; height: 4px; background: var(--navy); }
  .services-divider { left: 317px; top: 668px; width: 2px; height: 348px; background: var(--navy); opacity: .6; }

  .service-list { list-style: none; }
  .service-list.col-a { left: 62px; top: 668px; }
  .service-list.col-b { left: 348px; top: 668px; }
  .service-list li { position: relative; padding-left: 36px; font-size: 23px; font-weight: 500; color: var(--white); line-height: 29px; margin-bottom: 17px; }
  .service-list li svg { position: absolute; left: 0; top: 4px; }
  .service-more { left: 348px; top: 988px; font-size: 18px; color: var(--white); }

  .art-team { left: 560px; top: 58px; width: 422px; height: 380px; border-radius: 48% 52% 46% 54% / 50% 44% 56% 50%; background: radial-gradient(circle at 50% 45%, #2a2fb0 0%, var(--navy) 70%); border: 4px solid var(--white); }
  .art-exam { left: 584px; top: 475px; width: 406px; height: 460px; border-radius: 24px; background: linear-gradient(180deg, rgba(255,255,255,.12) 0%, rgba(222,170,90,.35) 100%); }

  .contact-band { left: 0; top: 1051px; width: 1000px; height: 245px; background: var(--ink); }
  .contact-bar { left: 60px; top: 1066px; width: 427px; height: 34px; background: var(--navy); overflow: hidden; }
  .contact-bar::after { content: ""; position: absolute; right: 0; top: 0; width: 150px; height: 34px; background: var(--blue-accent); clip-path: polygon(16% 0, 100% 0, 100% 100%, 0 100%); }
  .contact-bar span { position: relative; z-index: 1; display: block; padding-left: 18px; font-size: 17px; font-weight: 500; color: var(--white); line-height: 34px; letter-spacing: .3px; }
  .contact-list { left: 60px; top: 1128px; list-style: none; }
  .contact-list li { display: flex; align-items: center; gap: 20px; font-size: 20px; color: var(--white); height: 40px; margin-bottom: 1px; }
  .contact-list .icon { width: 26px; height: 26px; border-radius: 50%; background: var(--green-bright); display: flex; align-items: center; justify-content: center; flex: none; }

  .call-card { left: 597px; top: 940px; width: 358px; height: 356px; background: var(--navy); }
  .call-lead { left: 0; top: 20px; width: 358px; text-align: center; font-size: 21px; color: var(--white); }
  .call-frame { left: 21px; top: 51px; width: 319px; height: 128px; border: 3px solid var(--green-bright); }
  .call-phone { left: 0; top: 66px; width: 358px; text-align: center; font-weight: 700; font-size: 37px; color: var(--white); line-height: 1; }
  .call-name { left: 0; top: 114px; width: 358px; text-align: center; font-size: 31px; color: var(--white); line-height: 1; }
  .call-shelter { left: 79px; top: 150px; width: 200px; text-align: center; font-weight: 600; font-size: 48px; color: var(--green-bright); line-height: 1; background: var(--navy); letter-spacing: 1px; }
  .hours { left: 20px; top: 220px; width: 318px; height: 136px; background: var(--white); padding-top: 22px; }
  .hours p { margin: 0 auto 10px; width: 288px; text-align: center; font-weight: 700; font-size: 15px; color: var(--ink); border-bottom: 2px solid var(--green-bright); padding-bottom: 4px; }
</style>
</head>
<body>
<main class="flyer">

  <div class="abs brand">
    <span class="brand-dot"></span>
    <span class="brand-name">BrookPaw Vet</span>
  </div>

  <h1>
    <span class="abs headline-top">AUSTIN TX FIRST</span>
    <span class="abs headline-main">VETERINARY</span>
    <span class="abs headline-sub">URGENT CARE</span>
  </h1>
  <p class="abs tagline">We are the first veterinary urgent care animal<br>clinic in Austin Texas.</p>

  <div class="abs promise">
    <svg width="76" height="76" viewBox="0 0 76 76" aria-hidden="true">
      <path d="M22 0h24v22h22v24H46v22H22V46H0V22h22z" fill="var(--navy)"/>
      <circle cx="58" cy="58" r="17" fill="var(--white)" stroke="var(--navy)" stroke-width="3"/>
    </svg>
    <p class="promise-text">
      <span class="l1">We are <b>Affordable</b></span>
      <span class="l2">as well as family owned.</span>
    </p>
  </div>

  <h2 class="abs services-title">LIST OF <b>SERVICES</b></h2>
  <div class="abs services-rule"></div>
  <div class="abs services-divider"></div>

  <svg width="0" height="0" style="position:absolute">
    <defs>
      <g id="paw">
        <ellipse cx="11" cy="15" rx="6" ry="5" fill="var(--navy)"/>
        <circle cx="4" cy="9" r="2.6" fill="var(--navy)"/>
        <circle cx="8.5" cy="4.5" r="2.6" fill="var(--navy)"/>
        <circle cx="13.5" cy="4.5" r="2.6" fill="var(--navy)"/>
        <circle cx="18" cy="9" r="2.6" fill="var(--navy)"/>
      </g>
    </defs>
  </svg>

  <ul class="abs service-list col-a">
    <li><svg width="22" height="21"><use href="#paw"/></svg>Ear</li>
    <li><svg width="22" height="21"><use href="#paw"/></svg>Eye</li>
    <li><svg width="22" height="21"><use href="#paw"/></svg>Skin Issues</li>
    <li><svg width="22" height="21"><use href="#paw"/></svg>Limping</li>
    <li><svg width="22" height="21"><use href="#paw"/></svg>Broken Toenails</li>
    <li><svg width="22" height="21"><use href="#paw"/></svg>Lacerations</li>
    <li><svg width="22" height="21"><use href="#paw"/></svg>Coughing</li>
    <li><svg width="22" height="21"><use href="#paw"/></svg>Sneezing</li>
  </ul>
  <ul class="abs service-list col-b">
    <li><svg width="22" height="21"><use href="#paw"/></svg>Allergies</li>
    <li><svg width="22" height="21"><use href="#paw"/></svg>Vomiting and<br>Diarrhea</li>
    <li><svg width="22" height="21"><use href="#paw"/></svg>Urinary Issues</li>
    <li><svg width="22" height="21"><use href="#paw"/></svg>Constipation</li>
    <li><svg width="22" height="21"><use href="#paw"/></svg>Snake Bites</li>
    <li><svg width="22" height="21"><use href="#paw"/></svg>Toxin ingestion</li>
  </ul>
  <p class="abs service-more">&amp; many many more......</p>

  <div class="abs art-team" role="img" aria-label="Cartoon illustration of a waving veterinarian with a dog, a cat and a fluffy puppy on a dark blue blob"></div>
  <div class="abs art-exam" role="img" aria-label="Cartoon illustration of a vet examining a dog on a table beside a medicine cabinet, with pets and line icons of vet supplies"></div>

  <section class="abs contact-band"></section>
  <div class="abs contact-bar"><span>CONTACT INFORMATION</span></div>
  <ul class="abs contact-list">
    <li><span class="icon"><svg width="12" height="16" viewBox="0 0 12 16"><path d="M6 0a6 6 0 0 1 6 6c0 4-6 10-6 10S0 10 0 6a6 6 0 0 1 6-6z" fill="#fff"/><circle cx="6" cy="6" r="2.2" fill="var(--green-bright)"/></svg></span>4871 W Larkspur Rd Suite B212 Austin, Tx 78753</li>
    <li><span class="icon"><svg width="14" height="11" viewBox="0 0 14 11"><rect x="0.5" y="0.5" width="13" height="10" fill="#fff"/><path d="M1 1l6 5 6-5" stroke="var(--green-bright)" stroke-width="1.4" fill="none"/></svg></span>info@brookpawclinic.com</li>
    <li><span class="icon"><svg width="16" height="16" viewBox="0 0 16 16" fill="none" stroke="#fff" stroke-width="1.4"><circle cx="8" cy="8" r="6.5"/><ellipse cx="8" cy="8" rx="3" ry="6.5"/><path d="M1.5 8h13"/></svg></span>www.brookpawclinic.com</li>
  </ul>

  <aside class="abs call-card">
    <p class="abs call-lead">Call us to make appointment</p>
    <div class="abs call-frame"></div>
    <p class="abs call-phone">737-555-0148</p>
    <p class="abs call-name">Animal Clinic</p>
    <p class="abs call-shelter">SHELTER</p>
    <div class="abs hours">
      <p>MONDAY TO FRIDAY 12PM TO 9PM</p>
      <p>SATURDAY TO SUNDAY 10AM TO 6PM</p>
    </div>
  </aside>

</main>
</body>
</html>
```